Business Card Design for Training Business

Clear Path Coaching is a new business that delivers training and other services with a focus on topics related to mental health and wellbeing, for example, Wellmind Response Course, Resilience etc. We have a strong focus on evidence-based psychology and neuroscience. I have a logo which I will upload with the brief, so please consider colours that work well with the logo.
Target Market(s)
Adults, workplaces (particularly government and not-for-profits)
Industry/Entity Type
Business
Contact Information for Business Card
Head Strong TrainingSamantha SellwoodDirector0438 770 850sam@headstrongtraining.com.auwww.headstrongtraining.com.au

```html
<!DOCTYPE html>
<html lang="en">
<head>
<meta charset="utf-8">
<title>Clear Path Coaching – Business Card</title>
<link rel="stylesheet" href="https://fonts.googleapis.com/css2?family=Comfortaa:wght@300;400&family=Raleway:wght@300;400&display=swap">
<style>
  :root {
    --stage: #3b3b3b;
    --teal: #21b6bb;
    --teal-light: #5fd0d3;
    --paper: #f7f7f7;
    --brown: #4d403b;
    --ink: #5e5a58;
    --white: #ffffff;
  }
  * { margin: 0; padding: 0; box-sizing: border-box; }
  html, body { width: 1200px; height: 750px; overflow: hidden; }
  body {
    background: var(--stage);
    font-family: "Raleway", sans-serif;
    position: relative;
  }
  .card {
    position: absolute;
    left: 371px;
    width: 461px;
    height: 263px;
    border-radius: 14px;
    overflow: hidden;
    background: var(--teal);
  }
  .card--front { top: 106px; }
  .card--back { top: 387px; }
  .card__shape { position: absolute; inset: 0; width: 461px; height: 263px; }

  .brand {
    position: absolute;
    left: 0; right: 0;
    text-align: center;
  }
  .brand__mark {
    display: block;
    margin: 0 auto;
    border-radius: 50%;
  }
  .brand__name {
    display: block;
    font-family: "Raleway", sans-serif;
    font-weight: 300;
    letter-spacing: 3px;
    text-transform: uppercase;
  }
  .card--front .brand { top: 14px; }
  .card--front .brand__mark { width: 70px; height: 70px; border: 1.5px solid var(--teal); }
  .card--front .brand__name { margin-top: 20px; font-size: 19px; color: var(--ink); }

  .person { position: absolute; top: 145px; left: 0; right: 0; text-align: center; }
  .person__name {
    font-family: "Comfortaa", sans-serif;
    font-weight: 300;
    font-size: 18px;
    color: var(--teal);
  }
  .person__role { margin-top: 3px; font-size: 13px; color: var(--brown); }

  .contacts {
    position: absolute;
    top: 214px; left: 0; right: 0;
    color: var(--white);
    font-size: 12px;
    font-weight: 300;
    text-align: center;
    line-height: 18px;
  }
  .contacts__row { display: flex; justify-content: center; gap: 16px; }
  .contacts__item { display: inline-flex; align-items: center; gap: 5px; }
  .contacts__item svg { width: 11px; height: 11px; fill: var(--white); }

  .card--back .brand { top: 62px; }
  .card--back .brand__mark { width: 96px; height: 96px; border: 1.5px solid var(--white); }
  .card--back .brand__name { margin-top: 14px; font-size: 14px; color: var(--white); }
  .card--back .site {
    position: absolute;
    top: 227px; left: 0; right: 0;
    text-align: center;
    font-size: 12.5px;
    font-weight: 300;
    color: var(--white);
  }
</style>
</head>
<body>

<section class="card card--front">
  <svg class="card__shape" viewBox="0 0 461 263" aria-hidden="true">
    <path d="M0,64 C70,236 400,236 461,86" fill="none" stroke="var(--brown)" stroke-width="9"/>
    <path d="M0,0 H461 V86 C400,236 70,236 0,64 Z" fill="var(--paper)"/>
    <path d="M0,64 C70,236 400,236 461,86" fill="none" stroke="var(--teal-light)" stroke-width="2"/>
  </svg>

  <div class="brand">
    <span class="brand__mark"></span>
    <span class="brand__name">Clear Path Coaching</span>
  </div>

  <div class="person">
    <p class="person__name">Rebecca Tanfield</p>
    <p class="person__role">Director</p>
  </div>

  <div class="contacts">
    <div class="contacts__row">
      <span class="contacts__item">
        <svg viewBox="0 0 24 24"><path d="M6.6 10.8a15.1 15.1 0 0 0 6.6 6.6l2.2-2.2a1 1 0 0 1 1-.25 11.4 11.4 0 0 0 3.6.57 1 1 0 0 1 1 1V20a1 1 0 0 1-1 1A17 17 0 0 1 3 4a1 1 0 0 1 1-1h3.5a1 1 0 0 1 1 1c0 1.25.2 2.45.57 3.6a1 1 0 0 1-.25 1z"/></svg>
        0491 362 517
      </span>
      <span class="contacts__item">
        <svg viewBox="0 0 24 24"><path d="M2 5h20v14H2z M2 5l10 8 10-8" fill="var(--white)" stroke="var(--teal)" stroke-width="1.5"/></svg>
        bec@clearpathcoaching.example.au
      </span>
    </div>
    <div class="contacts__row">
      <span class="contacts__item">
        <svg viewBox="0 0 24 24"><circle cx="12" cy="12" r="10"/><path d="M2 12h20M12 2c3 3 3 17 0 20M12 2c-3 3-3 17 0 20" fill="none" stroke="var(--teal)" stroke-width="1.5"/></svg>
        www.clearpathcoaching.example.au
      </span>
    </div>
  </div>
</section>

<section class="card card--back">
  <div class="brand">
    <span class="brand__mark"></span>
    <span class="brand__name">Clear Path Coaching</span>
  </div>
  <p class="site">www.clearpathcoaching.example.au</p>
</section>

</body>
</html>
```